Agriculture Business Card

I want to use my existing logo and use my tagline of "Don't Guess...Soil Test" on the card. Looking for a double sided card that will really get peoples attention.
Contact Info:
Marlow Field Crop Edge
Calvin Brusk
2917 K Lane
Larkin, NE 68593
402-555-0193
calvin.r.brusk@fieldmailbox.net

```html
<!DOCTYPE html>
<html lang="en">
<head>
<meta charset="utf-8">
<title>Marlow Field Crop Edge – Business Card</title>
<link rel="stylesheet" href="https://fonts.googleapis.com/css2?family=Poppins:wght@400;600&family=Open+Sans:wght@600&display=swap">
<style>
  :root {
    --page: #141414;
    --card: #2a2a2c;
    --card-edge: #232325;
    --gold: #f5b318;
    --rust: #94614a;
    --ink: #d9d9d9;
    --rule: #4a4a4c;
    --ghost: #3a3a3c;
  }
  * { box-sizing: border-box; margin: 0; padding: 0; }
  html, body { width: 1200px; height: 820px; overflow: hidden; }
  body {
    background: var(--page);
    font-family: "Poppins", sans-serif;
    position: relative;
  }
  .card {
    position: absolute;
    width: 540px;
    height: 308px;
    background: var(--card);
    overflow: hidden;
  }
  .card--front {
    left: 40px; top: 256px;
    border-left: 3px solid var(--gold);
    border-bottom: 3px solid var(--gold);
  }
  .card--back {
    left: 620px; top: 256px;
    border-right: 3px solid var(--gold);
    border-bottom: 6px solid var(--gold);
  }

  /* Front */
  .brand {
    position: absolute;
    left: 150px; top: 44px;
    display: flex; align-items: center; gap: 16px;
  }
  .brand__dot {
    width: 74px; height: 74px; border-radius: 50%;
    background: var(--gold);
  }
  .brand__name {
    font-weight: 600; font-size: 22px; line-height: 1.15;
    color: var(--rust);
    width: 170px;
  }
  .divider {
    position: absolute; left: 150px; right: 40px; top: 150px;
    height: 1px; background: var(--rule);
  }
  .contact {
    position: absolute; left: 56px; top: 178px;
  }
  .contact__name {
    font-weight: 600; font-size: 20px; color: var(--gold);
    letter-spacing: 0.5px; text-transform: uppercase;
  }
  .contact__rule {
    width: 150px; height: 1px; background: var(--rule); margin: 6px 0 8px;
  }
  .contact__line {
    display: flex; align-items: center; gap: 8px;
    font-size: 13px; color: var(--ink); line-height: 1.45;
  }
  .contact__line svg { width: 13px; height: 13px; flex: none; }
  .contact__company {
    font-size: 14px; color: var(--gold); margin-top: 6px; line-height: 1.3;
  }
  .contact__address { font-size: 13px; color: var(--ink); line-height: 1.35; }

  /* Back */
  .emblem-field {
    position: absolute; left: 40px; top: 30px;
    width: 250px; height: 250px; border-radius: 50%;
    background: var(--ghost);
  }
  .back-brand {
    position: absolute; right: 34px; top: 150px;
    text-align: right;
  }
  .back-brand__name {
    font-weight: 600; font-size: 24px; line-height: 1.15; color: var(--rust);
    width: 210px; margin-left: auto;
  }
  .back-brand__tagline {
    font-family: "Open Sans", sans-serif; font-weight: 600;
    font-size: 17px; color: var(--gold); margin-top: 12px;
  }
</style>
</head>
<body>
  <section class="card card--front" aria-label="Business card front">
    <div class="brand">
      <span class="brand__dot"></span>
      <span class="brand__name">Marlow Field Crop Edge</span>
    </div>
    <div class="divider"></div>
    <div class="contact">
      <p class="contact__name">Calvin Brusk</p>
      <div class="contact__rule"></div>
      <p class="contact__line">
        <svg viewBox="0 0 16 16" aria-hidden="true"><path d="M3 1.5l3 3-1.5 2a9 9 0 0 0 5 5l2-1.5 3 3-2 2C7 15 1 9 1 3.5z" fill="var(--gold)"/></svg>
        402-555-0193
      </p>
      <p class="contact__line">
        <svg viewBox="0 0 16 16" aria-hidden="true"><rect x="1" y="3" width="14" height="10" fill="var(--gold)"/><path d="M1 3l7 6 7-6" fill="none" stroke="var(--card)" stroke-width="1.4"/></svg>
        calvin.r.brusk@fieldmailbox.net
      </p>
      <p class="contact__company">Marlow Field Crop Edge</p>
      <p class="contact__address">2917 K Lane, Larkin, NE 68593</p>
    </div>
  </section>

  <section class="card card--back" aria-label="Business card back">
    <div class="emblem-field"></div>
    <div class="back-brand">
      <p class="back-brand__name">Marlow Field Crop Edge</p>
      <p class="back-brand__tagline">Don't Guess...Soil Test</p>
    </div>
  </section>
</body>
</html>
```